Keystone Trench Co Business Card*

Looking for a professional, clean and crisp business card

I am in the underground utilities industry and am just looking for a really impressive business card. I would like our card to be white with our symbol crisp and clear with it protruding. I also have a business partner that will require his name and info on the card once the design is set. I would like to have our website info on the card which is;
http://keystonetrenchco.example/

Contact Information for Business Card

Website, contact name, number and email

```html
<!DOCTYPE html>
<html lang="en">
<head>
<meta charset="utf-8">
<title>Keystone Trench Co – Business Card</title>
<link rel="stylesheet" href="https://fonts.googleapis.com/css2?family=Saira+Condensed:wght@700&family=Montserrat:wght@400;500&display=swap">
<style>
  :root {
    --page-bg: #1c1c1e;
    --card-white: #ffffff;
    --card-dark: #0b0c0e;
    --card-dark-2: #1a1d22;
    --ink: #2b2f3a;
    --accent-blue: #3553a8;
    --logo-white: #ffffff;
  }
  * { margin: 0; padding: 0; box-sizing: border-box; }
  html, body {
    width: 1200px;
    height: 900px;
    overflow: hidden;
    background: var(--page-bg);
  }
  .canvas {
    position: relative;
    width: 1200px;
    height: 900px;
  }
  .card {
    position: absolute;
    left: 250px;
    width: 700px;
    height: 400px;
    overflow: hidden;
  }
  .card-back {
    top: 35px;
    background: var(--card-dark);
  }
  .back-pattern {
    position: absolute;
    inset: 0;
    background: linear-gradient(135deg, var(--card-dark-2) 0%, var(--card-dark) 55%, var(--card-dark-2) 100%);
  }
  .brand-mark {
    position: absolute;
    right: 44px;
    bottom: 54px;
    display: flex;
    align-items: center;
    gap: 12px;
  }
  .brand-dot {
    width: 18px;
    height: 18px;
    border-radius: 50%;
    background: var(--logo-white);
  }
  .brand-name {
    font-family: "Saira Condensed", "Arial Narrow", sans-serif;
    font-weight: 700;
    font-size: 34px;
    letter-spacing: 1px;
    text-transform: uppercase;
    color: var(--logo-white);
  }
  .card-front {
    top: 465px;
    background: var(--card-white);
  }
  .holder-name {
    position: absolute;
    left: 52px;
    top: 168px;
    font-family: "Saira Condensed", "Arial Narrow", sans-serif;
    font-weight: 700;
    font-size: 44px;
    letter-spacing: 1.5px;
    color: var(--ink);
    text-transform: uppercase;
  }
  .divider {
    position: absolute;
    left: 356px;
    top: 60px;
    width: 2px;
    height: 280px;
    background: var(--accent-blue);
  }
  .contact-list {
    position: absolute;
    left: 384px;
    top: 158px;
    list-style: none;
    font-family: "Montserrat", Arial, sans-serif;
    font-size: 17px;
    color: var(--ink);
  }
  .contact-item {
    display: flex;
    align-items: center;
    gap: 10px;
    height: 28px;
  }
  .contact-icon {
    width: 18px;
    height: 18px;
    flex: none;
  }
  .web-domain { color: var(--accent-blue); }
</style>
</head>
<body>
<div class="canvas">
  <section class="card card-back">
    <div class="back-pattern" role="img" aria-label="Dark diagonal pattern of pipe segments"></div>
    <div class="brand-mark">
      <span class="brand-dot"></span>
      <span class="brand-name">Keystone Trench Co</span>
    </div>
  </section>

  <section class="card card-front">
    <h1 class="holder-name">Dale Merrin</h1>
    <div class="divider"></div>
    <ul class="contact-list">
      <li class="contact-item">
        <svg class="contact-icon" viewBox="0 0 20 20" fill="none" stroke="#3553a8" stroke-width="1.5">
          <circle cx="10" cy="10" r="8.5"/>
          <path d="M7 6.2c-.6.5-.8 1.4-.3 2.5.9 2 2.4 3.6 4.5 4.6 1 .5 1.9.3 2.4-.3l-1.4-1.3-1.1.6c-1-.5-1.9-1.4-2.4-2.4l.6-1.1L8.2 6z"/>
        </svg>
        <span>778-555-0142</span>
      </li>
      <li class="contact-item">
        <svg class="contact-icon" viewBox="0 0 20 20" fill="none" stroke="#3553a8" stroke-width="1.5">
          <rect x="2" y="4.5" width="16" height="11"/>
          <path d="M2 4.5l8 6.5 8-6.5"/>
        </svg>
        <span>dale@keystonetrenchco.example</span>
      </li>
      <li class="contact-item">
        <svg class="contact-icon" viewBox="0 0 20 20" fill="none" stroke="#3553a8" stroke-width="1.5">
          <circle cx="10" cy="10" r="8"/>
          <ellipse cx="10" cy="10" rx="3.5" ry="8"/>
          <path d="M2 10h16M3.5 6h13M3.5 14h13"/>
        </svg>
        <span>www.<span class="web-domain">keystonetrenchco</span>.example</span>
      </li>
    </ul>
  </section>
</div>
</body>
</html>
```